Tovel & Associates - London New Letting and Property Management Company *

Tovel & Associates LTD is a new company based in London, and works with brand new residential property in the city centre.

We are aiming to have 1000 new properties a year.

We are looking for something modern and minimalistic :
Logo ,Monogram, Paper Head and Business Card.

Target Market(s)

Internation landlords

Industry/Entity Type

Real Estate

Logo Text

Tovel & Associates

Colors

Designer to choose colors to be used in the design.

Requirements
Nice to have
• A particular monogram with "TA"
Should not have
• Little House over the logo

```html
<!DOCTYPE html>
<html lang="en">
<head>
<meta charset="utf-8">
<title>Tovel &amp; Associates — Business Card</title>
<link rel="stylesheet" href="https://fonts.googleapis.com/css2?family=Montserrat:wght@400;500;600&display=swap">
<style>
  :root {
    --navy: #16508a;
    --navy-band: #1a4f85;
    --accent: #1f9ad6;
    --ink: #555a60;
    --paper: #ffffff;
    --backdrop: #2b2b2b;
  }
  * { margin: 0; padding: 0; box-sizing: border-box; }
  html, body { width: 1200px; height: 897px; overflow: hidden; }
  body {
    background: var(--backdrop);
    font-family: "Montserrat", sans-serif;
    position: relative;
  }
  .card {
    position: absolute;
    left: 303px;
    width: 595px;
    height: 338px;
    border-radius: 20px;
    overflow: hidden;
  }
  .card--front { top: 92px; background: var(--paper); }
  .card--back { top: 469px; background: var(--navy); }

  .name-band {
    position: absolute;
    left: 0; top: 27px;
    width: 470px; height: 70px;
    background: linear-gradient(90deg, var(--navy-band), #1d5a96);
    clip-path: polygon(0 0, 100% 0, calc(100% - 48px) 100%, 0 100%);
  }
  .band-square {
    position: absolute;
    left: 496px; top: 32px;
    width: 60px; height: 60px;
    background: var(--navy-band);
  }
  .holder-name {
    position: absolute; left: 29px; top: 44px;
    font-size: 19px; font-weight: 600; color: var(--accent);
    letter-spacing: 0.3px;
  }
  .holder-role {
    position: absolute; left: 29px; top: 69px;
    font-size: 15px; font-weight: 400; color: #fff;
  }
  .contact-list {
    position: absolute; left: 29px; top: 173px;
    list-style: none;
  }
  .contact-list li {
    display: flex; align-items: center;
    height: 20px;
    font-size: 15px; color: var(--ink);
  }
  .contact-list svg { width: 12px; height: 12px; margin-right: 9px; flex: none; }
  .address {
    position: absolute; left: 29px; top: 268px;
    font-size: 15px; line-height: 20px; color: var(--ink);
    font-style: normal;
  }
  .wordmark {
    position: absolute;
    display: flex; flex-direction: column; align-items: stretch;
    font-weight: 500;
    line-height: 1.1;
    text-align: center;
  }
  .wordmark .suffix {
    display: flex; align-items: center; justify-content: center;
    gap: 14px;
    color: var(--accent);
  }
  .wordmark .suffix::before,
  .wordmark .suffix::after {
    content: ""; flex: 1; height: 2px; background: var(--accent);
  }
  .card--front .wordmark {
    right: 36px; top: 256px;
    font-size: 27px; color: var(--navy);
  }
  .card--front .wordmark .suffix { font-size: 19px; gap: 12px; }
  .card--back .wordmark {
    left: 50%; transform: translateX(-50%); top: 184px;
    font-size: 34px; color: #fff;
  }
  .card--back .wordmark .suffix { font-size: 23px; gap: 16px; }
  .brand-square {
    position: absolute;
    left: 267px; top: 100px;
    width: 62px; height: 62px;
    background: var(--accent);
  }
</style>
</head>
<body>
  <section class="card card--front">
    <div class="name-band"></div>
    <div class="band-square"></div>
    <p class="holder-name">DANIEL ASHBY</p>
    <p class="holder-role">Founder</p>
    <ul class="contact-list">
      <li><svg viewBox="0 0 12 12"><rect x="3" y="0.8" width="6" height="10.4" rx="1.2" fill="none" stroke="#1f9ad6" stroke-width="1.3"/><line x1="5" y1="9.3" x2="7" y2="9.3" stroke="#1f9ad6" stroke-width="1"/></svg>020. 7946. 0381</li>
      <li><svg viewBox="0 0 12 12"><path d="M3 1.2 L4.8 1.2 L5.3 3.6 L4.2 4.4 C4.8 6.4 5.8 7.6 7.6 8.3 L8.4 7.2 L10.8 7.8 L10.8 9.8 C7 10.6 2.3 6.2 3 1.2Z" fill="#1f9ad6"/></svg>020. 7946. 0720</li>
      <li><svg viewBox="0 0 12 12"><rect x="1" y="2.5" width="10" height="7" rx="0.8" fill="none" stroke="#1f9ad6" stroke-width="1.2"/><path d="M1.4 3 L6 6.6 L10.6 3" fill="none" stroke="#1f9ad6" stroke-width="1.1"/></svg>info@tovelassociates.com</li>
      <li><svg viewBox="0 0 12 12"><circle cx="6" cy="6" r="5" fill="none" stroke="#1f9ad6" stroke-width="1.1"/><ellipse cx="6" cy="6" rx="2.2" ry="5" fill="none" stroke="#1f9ad6" stroke-width="0.9"/><line x1="1" y1="6" x2="11" y2="6" stroke="#1f9ad6" stroke-width="0.9"/></svg>www.tovelassociates.com</li>
    </ul>
    <address class="address">48 Harcourt Lane<br>London, EC2A 4RP</address>
    <p class="wordmark">Tovel &amp; Associates<span class="suffix">LTD</span></p>
  </section>

  <section class="card card--back">
    <div class="brand-square"></div>
    <p class="wordmark">Tovel &amp; Associates<span class="suffix">LTD</span></p>
  </section>
</body>
</html>
```